Redesign of business card for Cedar Ridge Mechanical

We are looking for a new design for our business cards for Cedar Ridge Mechanical. We are a plumbing & HVAC construction company, operating on the West Coast of Canada and USA. Logo attached.
Industry/Entity Type
Construction - Plumbing & HVAC
Contact Information for Business Card
Name, address, phone numbers, email, website address
Look and feel
Each slider illustrates characteristics of the customer's brand and the style your logo design should communicate.

```html
<!DOCTYPE html>
<html lang="en">
<head>
<meta charset="utf-8">
<title>Cedar Ridge Mechanical – Business Card</title>
<link href="https://fonts.googleapis.com/css2?family=Open+Sans:wght@400;600;700&display=swap" rel="stylesheet">
<style>
  :root {
    --backdrop: #e4e6e9;
    --card-white: #ffffff;
    --ink: #1e1e1e;
    --ink-soft: #7b7b7b;
    --rule: #555555;
    --sky-deep: #2a64be;
    --sky-mid: #5b93dc;
    --sky-haze: #c9dcf2;
    --city-light: #b9c2c8;
    --city-green: #6f8463;
    --ghost: #ededed;
  }
  * { margin: 0; padding: 0; box-sizing: border-box; }
  html, body { width: 1200px; height: 800px; overflow: hidden; }
  body {
    background: var(--backdrop);
    font-family: "Open Sans", Arial, sans-serif;
    position: relative;
  }
  .card {
    position: absolute;
    top: 245px;
    width: 540px;
    height: 309px;
    overflow: hidden;
    box-shadow: 0 6px 18px rgba(0,0,0,0.12);
  }
  .card--front { left: 40px; }
  .card--back { left: 620px; background: var(--card-white); }

  .front-photo {
    position: absolute; inset: 0;
    background:
      linear-gradient(160deg, rgba(255,255,255,0) 35%, rgba(240,246,252,0.55) 52%, rgba(255,255,255,0) 66%),
      linear-gradient(180deg, var(--sky-deep) 0%, var(--sky-mid) 30%, var(--sky-haze) 52%, var(--city-light) 64%, var(--city-green) 100%);
  }

  .brand-name {
    position: absolute;
    display: flex;
    align-items: center;
    color: var(--ink);
    font-weight: 700;
    text-transform: uppercase;
    letter-spacing: 0.04em;
  }
  .brand-name__mark {
    display: block;
    flex: none;
    border: 4px solid var(--ink);
  }
  .brand-name__text { line-height: 1.05; }

  .card--front .brand-name { left: 30px; top: 28px; gap: 16px; font-size: 34px; }
  .card--front .brand-name__mark { width: 74px; height: 74px; border-width: 5px; }

  .card--back .brand-name { left: 28px; top: 22px; gap: 12px; font-size: 20px; }
  .card--back .brand-name__mark { width: 46px; height: 46px; }

  .ghost-block {
    position: absolute;
    right: -30px; top: 92px;
    width: 250px; height: 250px;
    border: 20px solid var(--ghost);
    border-radius: 24px;
  }
  .person {
    position: absolute; left: 28px; top: 86px;
  }
  .person__name {
    font-size: 17px; font-weight: 700; color: var(--ink-soft);
    letter-spacing: 0.02em; line-height: 1.2;
  }
  .person__title {
    font-size: 13px; color: var(--ink); line-height: 1.3;
  }
  .title-rule {
    position: absolute; left: 150px; right: 0; top: 123px;
    height: 1px; background: var(--rule);
  }
  .contact-list {
    position: absolute; left: 28px; top: 140px;
    list-style: none;
  }
  .contact-list li {
    display: flex; align-items: center; gap: 8px;
    font-size: 13px; color: var(--ink);
    height: 24px;
  }
  .contact-list svg { width: 13px; height: 13px; flex: none; }
</style>
</head>
<body>

<section class="card card--front" aria-label="Card front">
  <div class="front-photo" role="img" aria-label="Photo of a waterfront city with an observation tower under a blue sky with streaks of cloud"></div>
  <div class="brand-name"><span class="brand-name__mark"></span><span class="brand-name__text">Cedar Ridge<br>Mechanical</span></div>
</section>

<section class="card card--back" aria-label="Card back">
  <div class="ghost-block" aria-hidden="true"></div>
  <div class="brand-name"><span class="brand-name__mark"></span><span class="brand-name__text">Cedar Ridge<br>Mechanical</span></div>

  <div class="person">
    <p class="person__name">DALE MERCER</p>
    <p class="person__title">President/Founder</p>
  </div>
  <div class="title-rule"></div>

  <ul class="contact-list">
    <li>
      <svg viewBox="0 0 16 16" aria-hidden="true"><path d="M3 1.5l3 .5 1 3-2 1.5a9 9 0 0 0 4.5 4.5L11 9l3 1 .5 3-2 1.5C6 14 2 10 1.5 3.5z" fill="#333"/></svg>
      213-555-0148
    </li>
    <li>
      <svg viewBox="0 0 16 16" aria-hidden="true"><rect x="1" y="3" width="14" height="10" fill="none" stroke="#333" stroke-width="1.5"/><path d="M1 3l7 6 7-6" fill="none" stroke="#333" stroke-width="1.5"/></svg>
      info@cedarridgemech.com
    </li>
    <li>
      <svg viewBox="0 0 16 16" aria-hidden="true"><circle cx="8" cy="8" r="6.5" fill="none" stroke="#333" stroke-width="1.3"/><ellipse cx="8" cy="8" rx="3" ry="6.5" fill="none" stroke="#333" stroke-width="1.1"/><path d="M1.5 8h13" stroke="#333" stroke-width="1.1"/></svg>
      www.cedarridgemech.com
    </li>
    <li>
      <svg viewBox="0 0 16 16" aria-hidden="true"><path d="M8 15s5-5.5 5-9A5 5 0 0 0 3 6c0 3.5 5 9 5 9z" fill="#333"/><circle cx="8" cy="6" r="1.8" fill="#fff"/></svg>
      2750 Harbor Line Rd, Suite #140 Tacoma, WA 98402
    </li>
  </ul>
</section>

</body>
</html>
```